Business card for my new company (Accounting firm)

I need a business card for my new business Brightwell Advisory and Ledger SA. Our services are accounting, tax, audit and financial management. Our customers are small companies, start-ups and new companies. The final design has to show financial security, trust and growth. Please find our logo attached to the business card. Text for the business card: Brightwell Advisory and Ledger SA Tomas Varenholt Director and Founder Certified Accountant Tel. 022 418 57 34 tv@clairevalconseil.ch www.clairevalconseil.ch Rue des Vergières 27 1201 Geneva
Target Market(s)
Our customers are small companies, start-ups and new companies.
Industry/Entity Type
Finance And Accounting
Contact Information for Business Card
Claireval Conseil et Comptes SA
Tomas Varenholt
Directeur et Fondateur
Expert-comptable diplômé
Tél. 022 418 57 34
tv@clairevalconseil.ch
www.clairevalconseil.ch
Rue des Vergières 27
1201 Genève

```html
<!DOCTYPE html>
<html lang="fr">
<head>
<meta charset="utf-8">
<title>Claireval Conseil et Comptes SA – Carte de visite</title>
<link href="https://fonts.googleapis.com/css2?family=Roboto:wght@400;500;700&display=swap" rel="stylesheet">
<style>
  :root {
    --backdrop: #3b3c3e;
    --card: #222326;
    --card-emboss: #6c7078;
    --blue: #2a9fd9;
    --blue-deep: #1a6aa3;
    --text-light: #f2f4f6;
  }
  * { margin: 0; padding: 0; box-sizing: border-box; }
  html, body {
    width: 799px; height: 1200px; overflow: hidden;
    background: var(--backdrop);
    font-family: "Roboto", Arial, sans-serif;
  }
  .card {
    position: absolute; left: 50px;
    width: 700px; height: 400px;
    background: var(--card);
    overflow: hidden;
    box-shadow: 0 12px 30px rgba(0,0,0,.45);
  }
  .card--front { top: 120px; }
  .card--back { top: 670px; }

  .front-band {
    position: absolute; left: 0; right: 0; bottom: 0; height: 16px;
    background: var(--blue);
  }
  .brand {
    position: absolute; display: flex; align-items: center; gap: 12px;
    font-weight: 500; letter-spacing: 1px; white-space: nowrap;
  }
  .brand__mark { width: 18px; height: 18px; flex: none; }
  .card--front .brand {
    left: 50%; top: 50%; transform: translate(-50%, -60%);
    font-size: 34px; color: var(--card-emboss);
  }
  .card--front .brand__mark { background: var(--card-emboss); width: 24px; height: 24px; }

  .person { position: absolute; left: 48px; top: 40px; }
  .person__name { color: var(--blue); font-size: 25px; font-weight: 700; }
  .person__role { color: var(--text-light); font-size: 14px; line-height: 1.35; margin-top: 4px; }

  .contact { position: absolute; left: 48px; top: 150px; list-style: none; }
  .contact li {
    display: flex; align-items: center; gap: 14px;
    color: var(--text-light); font-size: 17px; line-height: 27px;
  }
  .contact svg { width: 14px; height: 14px; fill: var(--blue); flex: none; }

  .accent-area {
    position: absolute; left: 0; right: 0; bottom: 0; height: 130px;
    background: linear-gradient(135deg, #2ba6e0 0%, #185f97 100%);
  }

  .card--back .brand {
    right: 40px; top: 170px; font-size: 22px; color: var(--text-light);
  }
  .card--back .brand__mark { background: var(--blue); }

  .address {
    position: absolute; right: 50px; bottom: 30px; width: 240px;
    text-align: center; color: var(--text-light); font-size: 18px; line-height: 1.45;
  }
</style>
</head>
<body>

<section class="card card--front" aria-label="Recto">
  <div class="brand"><span class="brand__mark"></span>Claireval Conseil et Comptes</div>
  <div class="front-band"></div>
</section>

<section class="card card--back" aria-label="Verso">
  <div class="accent-area" role="img" aria-label="Bandeau décoratif bleu en vagues"></div>

  <div class="person">
    <h1 class="person__name">Tomas Varenholt</h1>
    <p class="person__role">Directeur et Fondateur<br>Expert-comptable diplômé</p>
  </div>

  <ul class="contact">
    <li><svg viewBox="0 0 16 16"><path d="M3.5 1l2.5 3-1.5 1.8a9 9 0 0 0 5.7 5.7L12 10l3 2.5-1.3 2.3C8 15 1 8 1.2 2.3z"/></svg>022 418 57 34</li>
    <li><svg viewBox="0 0 16 16"><path d="M1 3h14v10H1z M2 4l6 5 6-5" fill="none" stroke="var(--blue)" stroke-width="1.6"/></svg>tv@clairevalconseil.ch</li>
    <li><svg viewBox="0 0 16 16"><circle cx="8" cy="8" r="6.5" fill="none" stroke="var(--blue)" stroke-width="1.5"/><path d="M1.5 8h13M8 1.5c-3 3.5-3 9.5 0 13M8 1.5c3 3.5 3 9.5 0 13" fill="none" stroke="var(--blue)" stroke-width="1.2"/></svg>www.clairevalconseil.ch</li>
  </ul>

  <div class="brand"><span class="brand__mark"></span>Claireval Conseil et Comptes</div>

  <p class="address">Rue des Vergières 27<br>1201 Genève</p>
</section>

</body>
</html>
```